Presentation for partners template design for a healthy bakery

A bakery that makes healthy homemade cupcakes, needs a presentation template for wholesale partners. We need 3-4 template pages with pictures and text blocks, one template that can accomodate a pricing table. Just to give you an idea for the templates our final presentation will include:
1. Cover page with logo
2. Intro page about us
3. Detailed description of products
4. Menu table: cupcakes with wholesale pricing
5. Contact page
Updates

Project Deadline Extended Reason: We feel we needed to extend the deadline to have more time to discuss and to give proper feedback to designers Added Tuesday, May 23, 2017

Target Market(s)

Food stores, cafés, fitness clubs, pastry shops, etc.

Industry/Entity Type

Bakery

Font styles to use
Sans Serif

Colors
fee3d4
fce8d3
eaf2ce
cadf82
ffffff
000000
cfeae6
ec1f27
86cfc6

Requirements
Must have
• Presentation needs to look serious and professional. The design needs to give an eco feel: we use recycled materials in our packaging and production. Please make sure the fonts you use support Cyrillic.
Nice to have
• The format of pages is either square or horizontal A4. The company mint colour (see logo attached) needs to be used, but other colours can be used in addition (lime green, peach, black, chocolate brown, red, etc). Craft paper texture (like our packaging, see photos) would be nice to have.

```html
<!DOCTYPE html>
<html lang="en">
<head>
<meta charset="utf-8">
<title>Wholesale Partner Presentation – Products &amp; Pricing Spread</title>
<link rel="stylesheet" href="https://fonts.googleapis.com/css2?family=Jost:wght@300;400;500&display=swap">
<style>
  :root {
    --backdrop: #9a9a9a;
    --paper: #ebe7e2;
    --paper-shade: #dcd8d3;
    --mint-deep: #4fb9ad;
    --mint: #6fcac0;
    --mint-light: #86cfc6;
    --mint-pale: #cfeae6;
    --ink: #2b2b2b;
    --rule: #a9a6a2;
    --white: #ffffff;
  }
  * { box-sizing: border-box; margin: 0; padding: 0; }
  html, body { width: 1200px; height: 900px; overflow: hidden; }
  body {
    background: var(--backdrop);
    font-family: "Jost", "Futura", sans-serif;
    color: var(--ink);
    position: relative;
  }
  .spread {
    position: absolute;
    left: 40px; top: 252px;
    width: 1120px; height: 396px;
    display: flex;
    box-shadow: 0 14px 30px rgba(0,0,0,.25);
  }
  .page {
    position: relative;
    width: 560px; height: 396px;
    background: var(--paper);
  }
  .page--left { background: linear-gradient(to right, var(--paper) 88%, var(--paper-shade)); }
  .page--right { background: linear-gradient(to left, var(--paper) 88%, var(--paper-shade)); }

  .section-tab {
    position: absolute;
    height: 26px;
    padding: 0 16px;
    display: flex; align-items: center;
    background: linear-gradient(to right, var(--mint-deep), var(--mint-light));
    color: var(--white);
    font-size: 13px; font-weight: 400;
    letter-spacing: .04em;
    text-transform: uppercase;
  }
  .page--left .section-tab { left: 36px; top: 26px; width: 250px; }

  .product { position: absolute; width: 270px; height: 150px; }
  .product__photo {
    position: absolute; left: 0; top: 0;
    width: 160px; height: 125px;
  }
  .product__note {
    position: absolute; left: 100px; top: 50px;
    width: 115px; height: 78px;
    padding: 8px 9px;
    background: rgba(79,185,173,.88);
    color: var(--white);
    font-size: 7px; line-height: 1.45; font-weight: 300;
  }
  .product--1 { left: 50px; top: 70px; }
  .product--2 { left: 292px; top: 70px; }
  .product--3 { left: 50px; top: 228px; }
  .product--4 { left: 292px; top: 228px; }

  .pricing {
    position: absolute; left: 40px; top: 20px;
    width: 440px;
    display: grid;
    grid-template-columns: 230px 80px 130px;
    font-size: 12.5px;
    text-transform: uppercase;
    letter-spacing: .03em;
  }
  .pricing__cell {
    height: 28px;
    display: flex; align-items: center; justify-content: center;
    border-bottom: 1px dashed var(--rule);
    border-right: 1px dashed var(--rule);
  }
  .pricing__cell--name { justify-content: flex-start; padding-left: 28px; }
  .pricing__title {
    height: 26px; border: none;
    background: var(--mint-deep); color: var(--white);
    justify-content: flex-start; padding-left: 16px; font-size: 13px;
  }
  .pricing__head {
    height: 26px; border: none;
    background: var(--mint-light); color: var(--white);
  }
  .pricing__head--price { background: var(--mint); }
  .pricing__band {
    background: linear-gradient(to right, var(--mint-deep), var(--mint-light));
    color: var(--white); border-right: none;
    justify-content: center; padding-left: 0;
  }
</style>
</head>
<body>
  <main class="spread">
    <section class="page page--left">
      <h2 class="section-tab">Description of products</h2>

      <article class="product product--1">
        <svg class="product__photo" role="img" aria-label="Photo of frosted cupcakes with pink and white cream" viewBox="0 0 160 125" preserveAspectRatio="none">
          <defs><linearGradient id="ph1" x1="0" y1="0" x2="1" y2="1"><stop offset="0" stop-color="#8fc7c9"/><stop offset=".6" stop-color="#c9a3a6"/><stop offset="1" stop-color="#7a6457"/></linearGradient></defs>
          <rect width="160" height="125" fill="url(#ph1)"/>
        </svg>
        <p class="product__note">Soft vanilla cupcakes with light cream, made from natural flour and a touch of honey.</p>
      </article>

      <article class="product product--2">
        <svg class="product__photo" role="img" aria-label="Photo of a cupcake topped with cream and sprinkles" viewBox="0 0 160 125" preserveAspectRatio="none">
          <defs><linearGradient id="ph2" x1="0" y1="0" x2="1" y2="1"><stop offset="0" stop-color="#6b5a47"/><stop offset=".5" stop-color="#e6dcb8"/><stop offset="1" stop-color="#b58a55"/></linearGradient></defs>
          <rect width="160" height="125" fill="url(#ph2)"/>
        </svg>
        <p class="product__note">Oat cookie base topped with whipped cream and sprinkles, baked fresh every morning.</p>
      </article>

      <article class="product product--3">
        <svg class="product__photo" role="img" aria-label="Photo of a tray of mini chocolate cupcakes" viewBox="0 0 160 125" preserveAspectRatio="none">
          <defs><linearGradient id="ph3" x1="0" y1="0" x2="1" y2="1"><stop offset="0" stop-color="#d9cfc8"/><stop offset=".5" stop-color="#5a3a2c"/><stop offset="1" stop-color="#c9b8a3"/></linearGradient></defs>
          <rect width="160" height="125" fill="url(#ph3)"/>
        </svg>
        <p class="product__note">Mini cocoa cupcakes with a light frosting, perfect for cafés and shared platters.</p>
      </article>

      <article class="product product--4">
        <svg class="product__photo" role="img" aria-label="Photo of berry cupcakes with pastel frosting" viewBox="0 0 160 125" preserveAspectRatio="none">
          <defs><linearGradient id="ph4" x1="0" y1="0" x2="1" y2="1"><stop offset="0" stop-color="#d8d2cf"/><stop offset=".5" stop-color="#c98a95"/><stop offset="1" stop-color="#9fb68e"/></linearGradient></defs>
          <rect width="160" height="125" fill="url(#ph4)"/>
        </svg>
        <p class="product__note">Berry cupcakes with fruit glaze and fresh toppings, low in sugar and full of taste.</p>
      </article>
    </section>

    <section class="page page--right">
      <div class="pricing" role="table" aria-label="Wholesale pricing">
        <div class="pricing__cell pricing__title">Wholesale pricing</div>
        <div class="pricing__cell pricing__head">Qty</div>
        <div class="pricing__cell pricing__head pricing__head--price">Price</div>

        <div class="pricing__cell pricing__cell--name pricing__band">Product name</div>
        <div class="pricing__cell">Qty</div><div class="pricing__cell">Price</div>

        <div class="pricing__cell pricing__cell--name">Product name</div><div class="pricing__cell">Qty</div><div class="pricing__cell">Price</div>
        <div class="pricing__cell pricing__cell--name">Product name</div><div class="pricing__cell">Qty</div><div class="pricing__cell">Price</div>
        <div class="pricing__cell pricing__cell--name">Product name</div><div class="pricing__cell">Qty</div><div class="pricing__cell">Price</div>
        <div class="pricing__cell pricing__cell--name">Product name</div><div class="pricing__cell">Qty</div><div class="pricing__cell">Price</div>
        <div class="pricing__cell pricing__cell--name">Product name</div><div class="pricing__cell">Qty</div><div class="pricing__cell">Price</div>
        <div class="pricing__cell pricing__cell--name">Product name</div><div class="pricing__cell">Qty</div><div class="pricing__cell">Price</div>
        <div class="pricing__cell pricing__cell--name">Product name</div><div class="pricing__cell">Qty</div><div class="pricing__cell">Price</div>
        <div class="pricing__cell pricing__cell--name">Product name</div><div class="pricing__cell">Qty</div><div class="pricing__cell">Price</div>
      </div>
    </section>
  </main>
</body>
</html>
```